App Design Project

Hello,
I'm looking for a great designer for my iOS Applications, we have a lot of works and we're short in designers :(
I want to revamp my thermometer iOS app. You will find attached the images I want to replace. I need something with the same element (temp, condition, weather icon) but with a different look!
Same, new icon, you have carte blanche to this one.
I want a design that stands out from the hundreds of weather application that almost all the same design. I am looking for something that does say "wow, it rocks."
Please do not Provide classic design that we can see everywhere ... I'm looking for something with a real artistic choice, contrast, colours, etc.
As a marketing screenshot, I want something classic, you'll find an example attached, feel free to innovate.
To sum-up :
- One new view for my App
- One new icon
- One marketing screenshot
Marketing

```html
<!DOCTYPE html>
<html lang="en">
<head>
<meta charset="utf-8">
<title>Weather App – Condition Views</title>
<link href="https://fonts.googleapis.com/css2?family=Advent+Pro:wght@200;300&family=Roboto+Condensed:wght@300;400;700&display=swap" rel="stylesheet">
<style>
  :root{
    --page-bg:#eeeeee;
    --white:#ffffff;
    --tag-bg:#2b2e34;
    --band-bg:rgba(22,26,34,.82);
    --band-line:rgba(255,255,255,.12);
    --ring-track:#1c2028;
    --accent:#2aa1e8;
    --bar-bg:#27a0e6;
    --rule:rgba(255,255,255,.55);
  }
  *{box-sizing:border-box;margin:0;padding:0}
  html,body{width:1200px;height:1000px;overflow:hidden}
  body{background:var(--page-bg);font-family:"Roboto Condensed",Arial,sans-serif;color:var(--white)}
  .board{
    display:grid;grid-template-columns:repeat(5,192px);grid-template-rows:repeat(2,341px);
    column-gap:39.5px;row-gap:149px;padding:82px 0 0 42px;
  }
  .screen{position:relative;width:192px;height:341px;overflow:hidden}
  .screen__backdrop{position:absolute;inset:0}
  .screen--partly .screen__backdrop{background:linear-gradient(170deg,#2f6fc0 0%,#5d97d6 45%,#c9dcee 80%,#eef3f8 100%)}
  .screen--mostly .screen__backdrop{background:linear-gradient(160deg,#355f8f 0%,#6d93bd 40%,#c2d3e4 70%,#5b83ad 100%)}
  .screen--overcast .screen__backdrop{background:linear-gradient(180deg,#2b3644 0%,#56616f 45%,#7b8590 70%,#3a4450 100%)}
  .screen--haze .screen__backdrop{background:linear-gradient(180deg,#485873 0%,#b98079 35%,#e38a68 60%,#c86f55 100%)}
  .screen--clear .screen__backdrop{background:linear-gradient(160deg,#a9c6ee 0%,#4f83d3 35%,#3a6cc2 70%,#6d9ae0 100%)}
  .screen--wind .screen__backdrop{background:linear-gradient(180deg,#5e716f 0%,#8c8566 40%,#b48b4c 70%,#6a5a3e 100%)}
  .screen--hail .screen__backdrop{background:linear-gradient(180deg,#6f82a4 0%,#95a4c0 45%,#b4c0d6 70%,#7a89a4 100%)}
  .screen--snow .screen__backdrop{background:linear-gradient(180deg,#7d92aa 0%,#aebccc 40%,#c8d2de 60%,#7c8ea5 100%)}
  .screen--thunder .screen__backdrop{background:linear-gradient(180deg,#233a58 0%,#3d6587 45%,#4f7b96 70%,#2c4766 100%)}
  .screen--fog .screen__backdrop{background:linear-gradient(180deg,#a9c3df 0%,#8eaacb 40%,#5f7fa2 70%,#34506f 100%)}

  .screen__tag{position:absolute;top:6px;right:0;background:var(--tag-bg);font-size:7px;font-weight:700;letter-spacing:.3px;padding:2px 6px 2px 7px}
  .screen__icon{position:absolute;top:30px;left:46px;width:100px;height:100px;fill:none;stroke:var(--white);stroke-width:5;stroke-linecap:round;stroke-linejoin:round}
  .screen__condition{position:absolute;top:134px;left:0;width:100%;text-align:center;font-family:"Advent Pro",sans-serif;font-weight:300;font-size:29px;letter-spacing:1px;line-height:36px;white-space:nowrap}
  .screen__rule{position:absolute;left:6px;right:6px;height:1px;background:var(--rule)}
  .screen__rule--upper{top:176px}
  .screen__rule--lower{top:231px}
  .temp{position:absolute;top:180px;left:0;width:100%;display:flex;justify-content:center;align-items:center;gap:8px}
  .temp__icon{width:10px;height:22px;fill:var(--white)}
  .temp__value{font-family:"Advent Pro",sans-serif;font-weight:200;font-size:40px;line-height:46px;letter-spacing:4px}
  .unit-toggle{position:absolute;top:212px;right:12px;display:flex;height:10px;font-size:6px}
  .unit-toggle__off{width:12px;background:#e8e8e8}
  .unit-toggle__on{width:12px;background:#1f2229;color:var(--accent);text-align:center;line-height:10px}
  .stats{position:absolute;top:241px;left:0;width:100%;height:55px;background:var(--band-bg);display:flex;align-items:center}
  .stats__half{height:100%;display:flex;align-items:center}
  .stats__half--wind{width:84px;padding-left:5px;gap:8px;border-right:1px solid var(--band-line)}
  .stats__half--dir{padding-left:12px;gap:8px}
  .stats__glyph{width:20px;height:14px;fill:none;stroke:var(--white);stroke-width:1.6;stroke-linecap:round}
  .stats__ring{position:relative;width:40px;height:40px}
  .stats__ring svg{width:40px;height:40px}
  .stats__ring span{position:absolute;inset:0;text-align:center;line-height:40px;font-size:11px;font-weight:300}
  .stats__drop{width:14px;height:14px}
  .stats__speed{font-size:13px;font-weight:300;letter-spacing:.6px}
  .forecast{position:absolute;top:296px;left:0;width:100%;height:45px;background:var(--bar-bg);display:flex;justify-content:space-around;padding:6px 2px 0}
  .forecast__day{display:flex;flex-direction:column;align-items:center;gap:3px;font-size:8px;font-weight:300}
  .forecast__day svg{width:17px;height:17px;fill:none;stroke:var(--white);stroke-width:6;stroke-linecap:round;stroke-linejoin:round}
</style>
</head>
<body>
<svg width="0" height="0" style="position:absolute" aria-hidden="true">
  <defs>
    <symbol id="i-cloud" viewBox="0 0 100 100"><path d="M28 74H72A16 16 0 0 0 74 42A23 23 0 0 0 30 41A17 17 0 0 0 28 74Z"/></symbol>
    <symbol id="i-sun" viewBox="0 0 100 100"><circle cx="50" cy="50" r="17"/><path d="M50 14V24M50 76V86M14 50H24M76 50H86M25 25L32 32M68 68L75 75M25 75L32 68M68 32L75 25"/></symbol>
    <symbol id="i-partly" viewBox="0 0 100 100"><circle cx="64" cy="38" r="14"/><path d="M64 12V16M86 38H90M82 20L79 23M46 20L49 23"/><path d="M24 84H60A13 13 0 0 0 62 58A19 19 0 0 0 26 57A14 14 0 0 0 24 84Z"/></symbol>
    <symbol id="i-mostly" viewBox="0 0 100 100"><path d="M50 40A18 18 0 0 1 84 44A12 12 0 0 1 82 68"/><path d="M22 80H64A14 14 0 0 0 66 52A20 20 0 0 0 26 50A15 15 0 0 0 22 80Z"/></symbol>
    <symbol id="i-haze" viewBox="0 0 100 100"><circle cx="50" cy="36" r="16"/><path d="M16 62H84M24 74H76M32 86H68"/></symbol>
    <symbol id="i-wind" viewBox="0 0 100 100"><path d="M12 38H64A10 10 0 1 0 54 28M12 54H82A10 10 0 1 1 72 64M12 70H52"/></symbol>
    <symbol id="i-hail" viewBox="0 0 100 100"><path d="M28 64A16 16 0 0 1 28 32A22 22 0 0 1 72 30A16 16 0 0 1 74 64"/><circle cx="38" cy="74" r="3" fill="#fff"/><circle cx="50" cy="84" r="3" fill="#fff"/><circle cx="62" cy="74" r="3" fill="#fff"/><circle cx="50" cy="66" r="3" fill="#fff"/></symbol>
    <symbol id="i-snow" viewBox="0 0 100 100"><path d="M28 64A16 16 0 0 1 28 32A22 22 0 0 1 72 30A16 16 0 0 1 74 64"/><path d="M50 62V88M39 68L61 82M39 82L61 68"/></symbol>
    <symbol id="i-thunder" viewBox="0 0 100 100"><path d="M28 66A16 16 0 0 1 28 34A22 22 0 0 1 72 32A16 16 0 0 1 74 66"/><path d="M54 52L42 72H54L46 90L64 66H52L58 52Z" fill="#fff"/></symbol>
    <symbol id="i-fog" viewBox="0 0 100 100"><path d="M16 36H70M30 50H84M16 64H70M30 78H84"/></symbol>
    <symbol id="i-rain" viewBox="0 0 100 100"><path d="M28 66A16 16 0 0 1 28 34A22 22 0 0 1 72 32A16 16 0 0 1 74 66"/><path d="M50 52V86M40 62L50 52L60 62"/></symbol>
    <symbol id="i-thermo" viewBox="0 0 10 22"><path d="M3 2A2 2 0 0 1 7 2V14A4 4 0 1 1 3 14Z"/></symbol>
    <symbol id="i-gust" viewBox="0 0 20 14"><path d="M1 5H14A2.5 2.5 0 1 0 11.5 2.5M1 9H17M3 12H12A2 2 0 1 1 10 14"/></symbol>
    <symbol id="i-ring" viewBox="0 0 40 40"><circle cx="20" cy="20" r="16" fill="none" stroke="#1c2028" stroke-width="5"/><circle cx="20" cy="20" r="16" fill="none" stroke="#2aa1e8" stroke-width="5" stroke-dasharray="55 101" transform="rotate(90 20 20)"/></symbol>
    <symbol id="i-drop" viewBox="0 0 14 14"><circle cx="7" cy="7" r="7" fill="#fff"/><path d="M7 3L9.5 7.5A2.5 2.5 0 1 1 4.5 7.5Z" fill="#1a1e26"/></symbol>
  </defs>
</svg>

<main class="board">
  <section class="screen screen--partly">
    <div class="screen__backdrop" role="img" aria-label="Photo of blue sky with scattered white clouds"></div>
    <div class="screen__tag">LONDON, UK</div>
    <svg class="screen__icon"><use href="#i-partly"/></svg>
    <h2 class="screen__condition">Partly Cloudy</h2>
    <div class="screen__rule screen__rule--upper"></div>
    <div class="temp"><svg class="temp__icon"><use href="#i-thermo"/></svg><span class="temp__value">9°C</span></div>
    <div class="unit-toggle"><span class="unit-toggle__off"></span><span class="unit-toggle__on">°C</span></div>
    <div class="screen__rule screen__rule--lower"></div>
    <div class="stats"><div class="stats__half stats__half--wind"><svg class="stats__glyph"><use href="#i-gust"/></svg><div class="stats__ring"><svg><use href="#i-ring"/></svg><span>30%</span></div></div><div class="stats__half stats__half--dir"><svg class="stats__drop"><use href="#i-drop"/></svg><span class="stats__speed">N 39 km/h</span></div></div>
    <nav class="forecast"><div class="forecast__day"><svg><use href="#i-partly"/></svg>MON</div><div class="forecast__day"><svg><use href="#i-hail"/></svg>TUES</div><div class="forecast__day"><svg><use href="#i-rain"/></svg>WEDS</div><div class="forecast__day"><svg><use href="#i-partly"/></svg>THURS</div><div class="forecast__day"><svg><use href="#i-sun"/></svg>FRI</div></nav>
  </section>

  <section class="screen screen--mostly">
    <div class="screen__backdrop" role="img" aria-label="Photo of bright cumulus clouds against blue sky"></div>
    <div class="screen__tag">LONDON, UK</div>
    <svg class="screen__icon"><use href="#i-mostly"/></svg>
    <h2 class="screen__condition">Mostly Cloudy</h2>
    <div class="screen__rule screen__rule--upper"></div>
    <div class="temp"><svg class="temp__icon"><use href="#i-thermo"/></svg><span class="temp__value">9°C</span></div>
    <div class="unit-toggle"><span class="unit-toggle__off"></span><span class="unit-toggle__on">°C</span></div>
    <div class="screen__rule screen__rule--lower"></div>
    <div class="stats"><div class="stats__half stats__half--wind"><svg class="stats__glyph"><use href="#i-gust"/></svg><div class="stats__ring"><svg><use href="#i-ring"/></svg><span>30%</span></div></div><div class="stats__half stats__half--dir"><svg class="stats__drop"><use href="#i-drop"/></svg><span class="stats__speed">N 39 km/h</span></div></div>
    <nav class="forecast"><div class="forecast__day"><svg><use href="#i-partly"/></svg>MON</div><div class="forecast__day"><svg><use href="#i-hail"/></svg>TUES</div><div class="forecast__day"><svg><use href="#i-rain"/></svg>WEDS</div><div class="forecast__day"><svg><use href="#i-partly"/></svg>THURS</div><div class="forecast__day"><svg><use href="#i-sun"/></svg>FRI</div></nav>
  </section>

  <section class="screen screen--overcast">
    <div class="screen__backdrop" role="img" aria-label="Photo of a dark grey overcast sky"></div>
    <div class="screen__tag">LONDON, UK</div>
    <svg class="screen__icon"><use href="#i-cloud"/></svg>
    <h2 class="screen__condition">Overcast</h2>
    <div class="screen__rule screen__rule--upper"></div>
    <div class="temp"><svg class="temp__icon"><use href="#i-thermo"/></svg><span class="temp__value">9°C</span></div>
    <div class="unit-toggle"><span class="unit-toggle__off"></span><span class="unit-toggle__on">°C</span></div>
    <div class="screen__rule screen__rule--lower"></div>
    <div class="stats"><div class="stats__half stats__half--wind"><svg class="stats__glyph"><use href="#i-gust"/></svg><div class="stats__ring"><svg><use href="#i-ring"/></svg><span>30%</span></div></div><div class="stats__half stats__half--dir"><svg class="stats__drop"><use href="#i-drop"/></svg><span class="stats__speed">N 39 km/h</span></div></div>
    <nav class="forecast"><div class="forecast__day"><svg><use href="#i-partly"/></svg>MON</div><div class="forecast__day"><svg><use href="#i-hail"/></svg>TUES</div><div class="forecast__day"><svg><use href="#i-rain"/></svg>WEDS</div><div class="forecast__day"><svg><use href="#i-partly"/></svg>THURS</div><div class="forecast__day"><svg><use href="#i-sun"/></svg>FRI</div></nav>
  </section>

  <section class="screen screen--haze">
    <div class="screen__backdrop" role="img" aria-label="Photo of an orange hazy sunset sky"></div>
    <div class="screen__tag">LONDON, UK</div>
    <svg class="screen__icon"><use href="#i-haze"/></svg>
    <h2 class="screen__condition">Haze</h2>
    <div class="screen__rule screen__rule--upper"></div>
    <div class="temp"><svg class="temp__icon"><use href="#i-thermo"/></svg><span class="temp__value">9°C</span></div>
    <div class="unit-toggle"><span class="unit-toggle__off"></span><span class="unit-toggle__on">°C</span></div>
    <div class="screen__rule screen__rule--lower"></div>
    <div class="stats"><div class="stats__half stats__half--wind"><svg class="stats__glyph"><use href="#i-gust"/></svg><div class="stats__ring"><svg><use href="#i-ring"/></svg><span>30%</span></div></div><div class="stats__half stats__half--dir"><svg class="stats__drop"><use href="#i-drop"/></svg><span class="stats__speed">N 39 km/h</span></div></div>
    <nav class="forecast"><div class="forecast__day"><svg><use href="#i-partly"/></svg>MON</div><div class="forecast__day"><svg><use href="#i-hail"/></svg>TUES</div><div class="forecast__day"><svg><use href="#i-rain"/></svg>WEDS</div><div class="forecast__day"><svg><use href="#i-partly"/></svg>THURS</div><div class="forecast__day"><svg><use href="#i-sun"/></svg>FRI</div></nav>
  </section>

  <section class="screen screen--clear">
    <div class="screen__backdrop" role="img" aria-label="Photo of a clear blue sky with sun rays"></div>
    <div class="screen__tag">LONDON, UK</div>
    <svg class="screen__icon"><use href="#i-sun"/></svg>
    <h2 class="screen__condition">Clear</h2>
    <div class="screen__rule screen__rule--upper"></div>
    <div class="temp"><svg class="temp__icon"><use href="#i-thermo"/></svg><span class="temp__value">9°C</span></div>
    <div class="unit-toggle"><span class="unit-toggle__off"></span><span class="unit-toggle__on">°C</span></div>
    <div class="screen__rule screen__rule--lower"></div>
    <div class="stats"><div class="stats__half stats__half--wind"><svg class="stats__glyph"><use href="#i-gust"/></svg><div class="stats__ring"><svg><use href="#i-ring"/></svg><span>30%</span></div></div><div class="stats__half stats__half--dir"><svg class="stats__drop"><use href="#i-drop"/></svg><span class="stats__speed">N 39 km/h</span></div></div>
    <nav class="forecast"><div class="forecast__day"><svg><use href="#i-partly"/></svg>MON</div><div class="forecast__day"><svg><use href="#i-hail"/></svg>TUES</div><div class="forecast__day"><svg><use href="#i-rain"/></svg>WEDS</div><div class="forecast__day"><svg><use href="#i-partly"/></svg>THURS</div><div class="forecast__day"><svg><use href="#i-sun"/></svg>FRI</div></nav>
  </section>

  <section class="screen screen--wind">
    <div class="screen__backdrop" role="img" aria-label="Photo of golden grass stalks bending in the wind"></div>
    <div class="screen__tag">LONDON, UK</div>
    <svg class="screen__icon"><use href="#i-wind"/></svg>
    <h2 class="screen__condition">Wind</h2>
    <div class="screen__rule screen__rule--upper"></div>
    <div class="temp"><svg class="temp__icon"><use href="#i-thermo"/></svg><span class="temp__value">9°C</span></div>
    <div class="unit-toggle"><span class="unit-toggle__off"></span><span class="unit-toggle__on">°C</span></div>
    <div class="screen__rule screen__rule--lower"></div>
    <div class="stats"><div class="stats__half stats__half--wind"><svg class="stats__glyph"><use href="#i-gust"/></svg><div class="stats__ring"><svg><use href="#i-ring"/></svg><span>30%</span></div></div><div class="stats__half stats__half--dir"><svg class="stats__drop"><use href="#i-drop"/></svg><span class="stats__speed">N 39 km/h</span></div></div>
    <nav class="forecast"><div class="forecast__day"><svg><use href="#i-partly"/></svg>MON</div><div class="forecast__day"><svg><use href="#i-hail"/></svg>TUES</div><div class="forecast__day"><svg><use href="#i-rain"/></svg>WEDS</div><div class="forecast__day"><svg><use href="#i-partly"/></svg>THURS</div><div class="forecast__day"><svg><use href="#i-sun"/></svg>FRI</div></nav>
  </section>

  <section class="screen screen--hail">
    <div class="screen__backdrop" role="img" aria-label="Close-up photo of hailstones"></div>
    <div class="screen__tag">LONDON, UK</div>
    <svg class="screen__icon"><use href="#i-hail"/></svg>
    <h2 class="screen__condition">Hail</h2>
    <div class="screen__rule screen__rule--upper"></div>
    <div class="temp"><svg class="temp__icon"><use href="#i-thermo"/></svg><span class="temp__value">9°C</span></div>
    <div class="unit-toggle"><span class="unit-toggle__off"></span><span class="unit-toggle__on">°C</span></div>
    <div class="screen__rule screen__rule--lower"></div>
    <div class="stats"><div class="stats__half stats__half--wind"><svg class="stats__glyph"><use href="#i-gust"/></svg><div class="stats__ring"><svg><use href="#i-ring"/></svg><span>30%</span></div></div><div class="stats__half stats__half--dir"><svg class="stats__drop"><use href="#i-drop"/></svg><span class="stats__speed">N 39 km/h</span></div></div>
    <nav class="forecast"><div class="forecast__day"><svg><use href="#i-partly"/></svg>MON</div><div class="forecast__day"><svg><use href="#i-hail"/></svg>TUES</div><div class="forecast__day"><svg><use href="#i-rain"/></svg>WEDS</div><div class="forecast__day"><svg><use href="#i-partly"/></svg>THURS</div><div class="forecast__day"><svg><use href="#i-sun"/></svg>FRI</div></nav>
  </section>

  <section class="screen screen--snow">
    <div class="screen__backdrop" role="img" aria-label="Photo of snow-covered mountains"></div>
    <div class="screen__tag">LONDON, UK</div>
    <svg class="screen__icon"><use href="#i-snow"/></svg>
    <h2 class="screen__condition">Snow</h2>
    <div class="screen__rule screen__rule--upper"></div>
    <div class="temp"><svg class="temp__icon"><use href="#i-thermo"/></svg><span class="temp__value">9°C</span></div>
    <div class="unit-toggle"><span class="unit-toggle__off"></span><span class="unit-toggle__on">°C</span></div>
    <div class="screen__rule screen__rule--lower"></div>
    <div class="stats"><div class="stats__half stats__half--wind"><svg class="stats__glyph"><use href="#i-gust"/></svg><div class="stats__ring"><svg><use href="#i-ring"/></svg><span>30%</span></div></div><div class="stats__half stats__half--dir"><svg class="stats__drop"><use href="#i-drop"/></svg><span class="stats__speed">N 39 km/h</span></div></div>
    <nav class="forecast"><div class="forecast__day"><svg><use href="#i-partly"/></svg>MON</div><div class="forecast__day"><svg><use href="#i-hail"/></svg>TUES</div><div class="forecast__day"><svg><use href="#i-rain"/></svg>WEDS</div><div class="forecast__day"><svg><use href="#i-partly"/></svg>THURS</div><div class="forecast__day"><svg><use href="#i-sun"/></svg>FRI</div></nav>
  </section>

  <section class="screen screen--thunder">
    <div class="screen__backdrop" role="img" aria-label="Photo of lightning bolts in a stormy blue sky"></div>
    <div class="screen__tag">LONDON, UK</div>
    <svg class="screen__icon"><use href="#i-thunder"/></svg>
    <h2 class="screen__condition">Thunderstorm</h2>
    <div class="screen__rule screen__rule--upper"></div>
    <div class="temp"><svg class="temp__icon"><use href="#i-thermo"/></svg><span class="temp__value">9°C</span></div>
    <div class="unit-toggle"><span class="unit-toggle__off"></span><span class="unit-toggle__on">°C</span></div>
    <div class="screen__rule screen__rule--lower"></div>
    <div class="stats"><div class="stats__half stats__half--wind"><svg class="stats__glyph"><use href="#i-gust"/></svg><div class="stats__ring"><svg><use href="#i-ring"/></svg><span>30%</span></div></div><div class="stats__half stats__half--dir"><svg class="stats__drop"><use href="#i-drop"/></svg><span class="stats__speed">N 39 km/h</span></div></div>
    <nav class="forecast"><div class="forecast__day"><svg><use href="#i-partly"/></svg>MON</div><div class="forecast__day"><svg><use href="#i-hail"/></svg>TUES</div><div class="forecast__day"><svg><use href="#i-rain"/></svg>WEDS</div><div class="forecast__day"><svg><use href="#i-partly"/></svg>THURS</div><div class="forecast__day"><svg><use href="#i-sun"/></svg>FRI</div></nav>
  </section>

  <section class="screen screen--fog">
    <div class="screen__backdrop" role="img" aria-label="Photo of misty blue mountain ridges"></div>
    <div class="screen__tag">LONDON, UK</div>
    <svg class="screen__icon"><use href="#i-fog"/></svg>
    <h2 class="screen__condition">Fog</h2>
    <div class="screen__rule screen__rule--upper"></div>
    <div class="temp"><svg class="temp__icon"><use href="#i-thermo"/></svg><span class="temp__value">9°C</span></div>
    <div class="unit-toggle"><span class="unit-toggle__off"></span><span class="unit-toggle__on">°C</span></div>
    <div class="screen__rule screen__rule--lower"></div>
    <div class="stats"><div class="stats__half stats__half--wind"><svg class="stats__glyph"><use href="#i-gust"/></svg><div class="stats__ring"><svg><use href="#i-ring"/></svg><span>30%</span></div></div><div class="stats__half stats__half--dir"><svg class="stats__drop"><use href="#i-drop"/></svg><span class="stats__speed">N 39 km/h</span></div></div>
    <nav class="forecast"><div class="forecast__day"><svg><use href="#i-partly"/></svg>MON</div><div class="forecast__day"><svg><use href="#i-hail"/></svg>TUES</div><div class="forecast__day"><svg><use href="#i-rain"/></svg>WEDS</div><div class="forecast__day"><svg><use href="#i-partly"/></svg>THURS</div><div class="forecast__day"><svg><use href="#i-sun"/></svg>FRI</div></nav>
  </section>
</main>
</body>
</html>
```